Transform Your Giving

I need a tri-fold brochure that will fit in a standard number 10 business envelope. Meadowlark and Allied Services is a charitable nonprofit. The goal of this brochure is to stimulate people into thinking about other ways to make a donation. The design should communicate the essential information on donation options, create a sense of professional integrity, be graphically sharp, easy to read and laid out in a way that doesn't make the material appear crowded.

```html
<!DOCTYPE html>
<html lang="en">
<head>
<meta charset="utf-8">
<title>Transform Your Giving – Tri-fold Brochure</title>
<link href="https://fonts.googleapis.com/css2?family=Montserrat:wght@500;600;700;800&family=Open+Sans:ital,wght@0,400;0,600;0,700;1,400;1,600&display=swap" rel="stylesheet">
<style>
:root{
  --navy:#2c2a5c;
  --navy-dark:#211f48;
  --green:#7cba3d;
  --green-dark:#5f9a2a;
  --ink:#3b3b4a;
  --paper:#ffffff;
  --stage:#e8e9ec;
  --photo-warm:#c9b8a6;
  --photo-soft:#dfe7d6;
}
*{box-sizing:border-box;margin:0;padding:0}
html,body{width:1200px;height:2872px;overflow:hidden;background:var(--stage)}
body{font-family:"Open Sans",Arial,sans-serif;color:var(--ink);position:relative}
.spread{position:absolute;left:40px;width:1120px;height:865px;display:flex;background:var(--paper);box-shadow:0 4px 18px rgba(0,0,0,.12)}
.spread--outside{top:541px}
.spread--inside{top:1466px}
.panel{position:relative;width:373.33px;height:100%;overflow:hidden;padding:26px 26px}
.panel+.panel{border-left:1px solid #eceef0}
h2,h3,h4{font-family:"Montserrat",Arial,sans-serif}
p{font-size:11px;line-height:1.55;margin-bottom:9px}
.photo{display:block;width:100%}
.impact-title{color:var(--navy);font-size:17px;font-weight:800;margin:18px 0 8px;letter-spacing:.3px}
.check-list{list-style:none;display:grid;grid-template-columns:1fr 1fr;gap:8px 10px;margin-top:12px}
.check-list li{font-size:12px;font-weight:700;color:var(--navy);display:flex;align-items:center;gap:7px}
.dot{width:9px;height:9px;border-radius:50%;background:var(--green);flex:none}
.center{text-align:center}
.lead{color:var(--navy);font-weight:700;font-size:12px;line-height:1.5}
.green-italic{color:var(--green-dark);font-style:italic;font-weight:600;font-size:13px;line-height:1.45;margin:14px 0}
.brand{display:flex;align-items:center;justify-content:center;gap:9px;margin:18px 0 4px}
.brand__mark{width:22px;height:22px;border-radius:50%;background:var(--green);flex:none}
.brand__name{font-family:"Montserrat",Arial,sans-serif;font-weight:800;font-size:15px;color:var(--navy);line-height:1.15;text-align:left}
.brand--light .brand__name{color:#fff}
.contact-title{font-family:"Montserrat",Arial,sans-serif;font-size:15px;font-weight:800;color:var(--navy);margin-top:22px}
.contact-sub{color:var(--green-dark);font-weight:700;font-size:11px;margin-bottom:10px}
.contact-line{font-size:11px;line-height:1.6;color:var(--ink)}
.follow{margin-top:14px;font-family:"Montserrat",Arial,sans-serif;font-weight:800;color:var(--navy);font-size:12px;display:flex;align-items:center;justify-content:center;gap:6px}
.follow span.c{width:14px;height:14px;border-radius:50%;background:var(--green);display:inline-block}
.cover{padding:0}
.cover__top{padding:30px 26px 0}
.cover__title{font-size:27px;font-weight:800;color:var(--navy);line-height:1.1}
.cover__tag{font-size:19px;font-weight:700;color:var(--green-dark);margin:6px 0 8px}
.cover__sub{font-size:11.5px;font-weight:600;color:var(--navy);line-height:1.45}
.cover__band{position:absolute;left:0;right:0;bottom:0;height:440px;background:var(--navy)}
.cover__band svg{position:absolute;left:0;top:-60px}
.icon-grid{position:absolute;left:20px;right:20px;top:120px;display:grid;grid-template-columns:repeat(3,1fr);gap:22px 8px}
.icon-item{text-align:center;color:#fff;font-family:"Montserrat",Arial,sans-serif;font-weight:700;font-size:11px;line-height:1.25}
.icon-circle{width:58px;height:58px;border-radius:50%;background:#fff;border:3px solid var(--green);margin:0 auto 7px;display:flex;align-items:center;justify-content:center}
.section{margin-bottom:14px}
.section__head{display:flex;align-items:center;gap:10px;margin-bottom:8px}
.badge{width:44px;height:44px;border-radius:50%;background:var(--navy);border:3px solid var(--green);flex:none;display:flex;align-items:center;justify-content:center}
.section__title{font-size:13.5px;font-weight:800;color:var(--navy);line-height:1.25}
.section__title em{display:block;font-style:italic;color:var(--green-dark);font-size:12px;font-weight:700}
.subhead{font-family:"Montserrat",Arial,sans-serif;font-size:12px;font-weight:800;color:var(--navy);margin:6px 0 4px}
.bullets{list-style:none;margin-bottom:9px}
.bullets li{font-size:11px;line-height:1.5;padding-left:14px;position:relative;margin-bottom:5px}
.bullets li::before{content:"";position:absolute;left:0;top:5px;width:7px;height:7px;border-radius:50%;background:var(--green)}
.green-line{height:3px;background:var(--green);width:60px;margin:4px 0 12px}
</style>
</head>
<body>

<!-- Outside spread -->
<section class="spread spread--outside" aria-label="Brochure outside">
  <div class="panel">
    <div class="photo" role="img" aria-label="Photo of a caregiver holding hands with an elderly woman" style="height:250px;margin:-26px -26px 0;width:calc(100% + 52px);background:linear-gradient(135deg,var(--photo-soft),var(--photo-warm))"></div>
    <h2 class="impact-title">THE IMPACT OF YOUR GIFT</h2>
    <p>Your generosity drives our mission. With every Smart gift you're supporting Meadowlark and Allied Services and our community of Smart Givers today and making an enduring impact.</p>
    <p>You can make a significantly larger impact when you donate long-term appreciated securities, including stock, mutual funds and bonds, directly to your favorite charity. Smart Giving lets you give more while keeping more for the causes you love.</p>
    <p>Explore how Smart Giving works for you with one of these simple options:</p>
    <ul class="check-list">
      <li><span class="dot"></span>DAFs</li>
      <li><span class="dot"></span>Stocks and Securities</li>
      <li><span class="dot"></span>QCDs</li>
      <li><span class="dot"></span>Charitable Annuity</li>
      <li><span class="dot"></span>Crypto</li>
    </ul>
  </div>

  <div class="panel center">
    <p class="lead" style="margin-top:18px">To learn more about Smart Giving Options and how they can benefit you and Meadowlark and Allied Services, and how those benefits can be shared, please reach out to our team. We're here to help you navigate these giving methods and answer any questions you may have.</p>
    <p class="green-italic">Being smart in giving is a way of being good to yourself,<br>those you love, and<br>the causes you cherish.</p>
    <p class="lead" style="font-weight:600">If you do not have a will, go to<br><span style="color:var(--green-dark);font-weight:700">www.EasyWillPlan.org</span><br>in 20 minutes you can have<br>a legal will – for free.</p>
    <div class="brand"><span class="brand__mark"></span><span class="brand__name">Meadowlark and<br>Allied Services</span></div>
    <h3 class="contact-title">CONTACT US</h3>
    <p class="contact-sub">Here is how to get in touch with us<br>at Meadowlark and Allied Services</p>
    <p class="contact-line">214 Harbor Lane<br>Suite 8, Fairview, ND 58000</p>
    <p class="contact-line">(555) 013-2640</p>
    <p class="contact-line">giving@meadowlarkallied.org<br>www.meadowlarkallied.org</p>
    <div class="follow">FOLLOW US <span class="c"></span><span class="c"></span></div>
  </div>

  <div class="panel cover">
    <div class="cover__top">
      <h1 class="cover__title" style="font-family:Montserrat,Arial,sans-serif">Transform Your Giving</h1>
      <h2 class="cover__tag">Be Strategic, Be Smart</h2>
      <p class="cover__sub">Discover the Impact of Smart Giving with Meadowlark and Allied Services</p>
    </div>
    <div role="img" aria-label="Photo of a smiling senior couple" style="position:absolute;left:0;right:0;top:170px;height:290px;background:linear-gradient(160deg,#e7dccd,var(--photo-warm))"></div>
    <div class="cover__band">
      <svg width="374" height="90" viewBox="0 0 374 90" aria-hidden="true">
        <path d="M0 60 L374 10 L374 60 L0 90 Z" fill="var(--navy)"/>
        <path d="M0 48 L374 0 L374 10 L0 60 Z" fill="var(--green)"/>
      </svg>
      <div class="brand brand--light" style="margin:20px 0 0"><span class="brand__mark"></span><span class="brand__name">Meadowlark and<br>Allied Services</span></div>
      <div class="icon-grid">
        <div class="icon-item"><div class="icon-circle"><svg width="28" height="28" viewBox="0 0 28 28"><circle cx="14" cy="14" r="11" fill="none" stroke="var(--navy)" stroke-width="2.5"/><path d="M11 8v12M15 8v12M10 9h6a3 3 0 010 5h-6m0 0h7a3 3 0 010 6h-7" fill="none" stroke="var(--navy)" stroke-width="2"/></svg></div>CRYPTO</div>
        <div class="icon-item"><div class="icon-circle"><svg width="28" height="28" viewBox="0 0 28 28"><rect x="5" y="10" width="18" height="13" rx="2" fill="var(--navy)"/><path d="M9 10V7h10v3" fill="none" stroke="var(--navy)" stroke-width="2"/><circle cx="14" cy="16" r="2.5" fill="var(--green)"/></svg></div>DAF'S</div>
        <div class="icon-item"><div class="icon-circle"><svg width="28" height="28" viewBox="0 0 28 28"><path d="M6 20l6-6 4 4 7-8" fill="none" stroke="var(--navy)" stroke-width="2.5"/><path d="M19 10h4v4" fill="none" stroke="var(--green)" stroke-width="2.5"/></svg></div>QCDS</div>
        <div class="icon-item" style="grid-column:1/2;margin-left:50px"><div class="icon-circle"><svg width="28" height="28" viewBox="0 0 28 28"><rect x="6" y="14" width="4" height="9" fill="var(--navy)"/><rect x="12" y="10" width="4" height="13" fill="var(--green)"/><rect x="18" y="6" width="4" height="17" fill="var(--navy)"/></svg></div>STOCKS &amp;<br>SECURITIES</div>
        <div class="icon-item" style="grid-column:2/4;margin-right:50px"><div class="icon-circle"><svg width="28" height="28" viewBox="0 0 28 28"><path d="M14 23s-9-5.5-9-11a5 5 0 019-3 5 5 0 019 3c0 5.5-9 11-9 11z" fill="var(--navy)"/><path d="M11 14h6M14 11v6" stroke="var(--green)" stroke-width="2"/></svg></div>CHARITABLE<br>ANNUITY</div>
      </div>
    </div>
  </div>
</section>

<!-- Inside spread -->
<section class="spread spread--inside" aria-label="Brochure inside">
  <div class="panel">
    <p>We would like to introduce you to five Strategic and Smart ways to give that could potentially be more beneficial to you compared to traditional cash donations. We encourage you to keep this information as a guide for your future contributions.</p>
    <div class="section">
      <div class="section__head"><span class="badge"><svg width="22" height="22" viewBox="0 0 22 22"><rect x="3" y="11" width="3" height="8" fill="#fff"/><rect x="9" y="7" width="3" height="12" fill="var(--green)"/><rect x="15" y="3" width="3" height="16" fill="#fff"/></svg></span>
        <h3 class="section__title">Gifts of Stocks or Appreciated Assets<em>Strategic &amp; Smart</em></h3></div>
      <p style="color:var(--green-dark);font-weight:600;font-style:italic">Consider your long-term publicly traded stock as a way to give to your favorite charity.</p>
      <h4 class="subhead">How Does It Work?</h4>
      <p>When you donate stock to a charity, you will generally get a tax deduction for the full market value of the stock on the date of the gift. Your contribution &amp; tax deduction may be significantly higher than contributing the after-tax proceeds. You also generally will not owe any capital gains tax on the appreciation.</p>
    </div>
    <div class="section">
      <div class="section__head"><span class="badge"><svg width="22" height="22" viewBox="0 0 22 22"><rect x="3" y="8" width="16" height="11" rx="2" fill="#fff"/><circle cx="11" cy="13.5" r="2.5" fill="var(--green)"/></svg></span>
        <h3 class="section__title">Donor Advised Fund (DAF):<em>Strategic &amp; Smart</em></h3></div>
      <p style="color:var(--green-dark);font-weight:600;font-style:italic">Consider a DAF – a simple, flexible, and tax-efficient way to support your favorite charities.</p>
      <p>A Donor Advised Fund (DAF) is like a charitable investment account for the sole purpose of supporting charitable organizations. You make a contribution, receive an immediate tax deduction, and then recommend grants from the fund to your favorite charities over time. Those funds can be invested for tax-free growth.</p>
    </div>
  </div>

  <div class="panel">
    <div class="section">
      <div class="section__head"><span class="badge"><svg width="22" height="22" viewBox="0 0 22 22"><path d="M4 16l5-5 3 3 6-7" fill="none" stroke="#fff" stroke-width="2.2"/></svg></span>
        <h3 class="section__title">Qualified Charitable Distributions (QCDs)<em>Strategic &amp; Smart</em></h3></div>
      <p style="color:var(--green-dark);font-weight:600;font-style:italic">Consider a QCD – if you're 70½ or older, an IRA distribution straight to charity.</p>
      <p>This option is for you if you're 70½ or older and would like to take a distribution from your IRA to charity tax-free each year. These transfers count toward your required minimum distribution.</p>
      <h4 class="subhead">How Does It Work?</h4>
      <p>You could be required to make a minimum distribution (RMD) from your IRA but do not need the funds. Consider a Qualified Charitable Distribution. Normally, distributions from a traditional IRA are taxable. But through a QCD, these distributions become tax-free when paid directly from the IRA to your favorite eligible charity. An IRA owner wishing to make a QCD should contact the IRA trustee well ahead of time to complete the transaction before the end of the year.</p>
    </div>
    <div class="section">
      <div class="section__head"><span class="badge"><svg width="22" height="22" viewBox="0 0 22 22"><path d="M11 18s-7-4.3-7-8.6a4 4 0 017-2.4 4 4 0 017 2.4C18 13.7 11 18 11 18z" fill="#fff"/></svg></span>
        <h3 class="section__title">Charitable Gift Annuity<em>Strategic &amp; Smart</em></h3></div>
      <p>You make a donation to a charity today. The gift is set up in return for a stream of income.</p>
      <h4 class="subhead">How Does It Work?</h4>
      <p>A charitable gift annuity is a contract between a donor and a charity. In return, you make a sizable gift to charity using cash, securities, or other assets. The charity in turn pays a fixed income for the rest of your life, and whatever remains at your passing supports the mission you love.</p>
    </div>
  </div>

  <div class="panel">
    <div class="section">
      <div class="section__head"><span class="badge"><svg width="22" height="22" viewBox="0 0 22 22"><circle cx="11" cy="11" r="8" fill="none" stroke="#fff" stroke-width="2"/><path d="M9 6v10M12 6v10M8 7h5a2 2 0 010 4H8m0 0h5.5a2 2 0 010 4H8" fill="none" stroke="var(--green)" stroke-width="1.6"/></svg></span>
        <h3 class="section__title">Cryptocurrency<em>Strategic &amp; Smart</em></h3></div>
      <p style="color:var(--green-dark);font-weight:600;font-style:italic">Consider donating Bitcoin and other cryptocurrencies to the charities you support.</p>
      <p>Bitcoin and other cryptocurrencies can be donated to charity just like other appreciated assets such as stocks and other business interests. Often you can deduct its value and avoid capital gains tax on the growth.</p>
      <h4 class="subhead">How Does It Work?</h4>
      <ul class="bullets">
        <li>Your tax deduction will be equal to the fair market value of the donated asset, as determined by a qualified appraisal.</li>
        <li>Non-cryptocurrency donation is tax-smart because it may eliminate capital gains taxes on the value you would owe after a sale.</li>
        <li>Charity will receive 100% of the value of the contribution.</li>
      </ul>
      <p>When charities are not able to accept direct cryptocurrency donations, a Donor Advised Fund (DAF) is a great way to donate these assets.</p>
    </div>
    <div role="img" aria-label="Photo of an older couple enjoying time together outdoors" style="position:absolute;left:26px;right:26px;bottom:26px;height:165px;background:linear-gradient(135deg,var(--photo-soft),#b9c9a6);border-right:6px solid var(--green);border-bottom:6px solid var(--green)"></div>
  </div>
</section>

</body>
</html>
```